Communications Consultancy needs Print Design Project

We are a communications consultancy providing training and services for organisations and individuals.

We have developed a Project Communication Strategy Model that is sound in functionality but poor in graphical design and structure.

We need to create a single page document that is a practical and profession tool to guide Project Managers through the process of communicating project outcomes.

The model will be used as a hard copy resource and will also need to be replicated onto a PowerPoint slide for instructional purposes.

Target Market(s)

Project Management Professionals

Industry/Entity Type

Communications

Requirements
Must have
• Icons to represent the different communication mediums (icons shown in attachment are just for example)

Enable future editing and be transfereable to PowerPoint

Have the company Logo (this can be privided as vector file etc.

Company contact details, website, phone, ABN etc.

```html
<!DOCTYPE html>
<html lang="en">
<head>
<meta charset="utf-8">
<title>Project Communication Strategy Model</title>
<link rel="stylesheet" href="https://fonts.googleapis.com/css2?family=Lato:wght@400;700;900&family=Nunito+Sans:wght@400;600;700&display=swap">
<style>
  :root{
    --green:#8fbf3a;
    --green-line:#9cc64a;
    --green-soft:#b9d98c;
    --ink:#2b2b2b;
    --dark-box:#333333;
    --grid:#8a8a8a;
    --grid-soft:#c9c9c9;
    --row-shade:#f0f0f2;
    --paper:#ffffff;
  }
  *{box-sizing:border-box;margin:0;padding:0}
  html,body{width:1200px;height:848px;overflow:hidden;background:var(--paper)}
  body{font-family:"Nunito Sans",Arial,sans-serif;color:var(--ink)}
  .sheet{position:relative;width:1200px;height:848px;overflow:hidden;background:var(--paper)}
  .abs{position:absolute}

  .title{left:31px;top:50px;font-size:24px;font-weight:400;letter-spacing:.2px}
  .brand{right:42px;top:34px;display:flex;align-items:center;gap:12px;font-family:"Lato",Arial,sans-serif;font-weight:900;font-size:33px;color:var(--ink);letter-spacing:-.5px}
  .brand-mark{width:18px;height:18px;background:var(--green)}

  .flow-lines{left:0;top:0;width:1200px;height:848px}

  .node{display:flex;align-items:center;justify-content:center;background:var(--dark-box);color:#fff;border-radius:4px;font-size:17px;font-weight:600}
  .node--event{left:490px;top:116px;width:199px;height:38px;font-size:19px}
  .node--yes{left:412px;top:209px;width:79px;height:38px}
  .node--no{left:672px;top:209px;width:79px;height:38px}
  .node--end{left:832px;top:209px;width:79px;height:38px}
  .question{left:603px;top:169px;font-size:14px;font-weight:600}

  .section-bar{display:flex;align-items:center;justify-content:center;background:var(--green);border-radius:5px;font-size:20px;font-weight:600;color:var(--ink)}
  .bar--channel{left:28px;top:280px;width:223px;height:38px}
  .bar--medium{left:287px;top:280px;width:480px;height:38px}
  .bar--delivery{left:796px;top:280px;width:361px;height:38px}
  .sub-bar{display:flex;align-items:center;justify-content:center;background:var(--green);border-radius:4px;font-size:15px;font-weight:600}
  .sub--technique{left:796px;top:339px;width:199px;height:29px}
  .sub--priority{left:1036px;top:339px;width:121px;height:29px}

  .audience{left:31px;width:225px;height:93px;border:1.5px solid var(--green-soft);border-radius:3px;display:flex}
  .audience--management{top:417px}
  .audience--stakeholders{top:511px}
  .audience--team{top:605px}
  .audience-id{width:76px;display:flex;flex-direction:column;align-items:center;justify-content:flex-end;padding-bottom:6px}
  .audience-id svg{width:50px;height:54px;margin-bottom:4px}
  .audience-name{font-size:9.5px;font-weight:700}
  .audience-list{list-style:none;padding-top:2px;flex:1;padding-right:10px}
  .audience-list li{font-size:9px;font-weight:700;height:18.6px;display:flex;align-items:flex-end}
  .audience-list li span{flex:1;border-bottom:1.5px dotted #555;margin-left:2px;height:8px}

  .medium-labels{left:287px;top:358px;width:480px;display:grid;grid-template-columns:repeat(6,1fr)}
  .medium-labels span{font-size:10px;font-weight:600;transform:rotate(-14deg);transform-origin:left bottom;padding-left:22px;white-space:nowrap}

  .matrix{display:grid;border:1px solid var(--grid)}
  .matrix > div{border-right:1px solid var(--grid);border-bottom:1px solid var(--grid)}
  .matrix--medium{left:287px;top:390px;width:480px;height:308px;grid-template-columns:repeat(6,1fr);grid-template-rows:27px 93px 93px 1fr}
  .matrix--technique{left:796px;top:390px;width:200px;height:308px;grid-template-columns:repeat(4,1fr);grid-template-rows:27px 93px 93px 1fr;border-color:var(--grid-soft)}
  .matrix--priority{left:1036px;top:390px;width:121px;height:308px;grid-template-columns:repeat(3,1fr);grid-template-rows:27px 93px 93px 1fr;border-color:var(--grid-soft)}
  .matrix--technique > div,.matrix--priority > div{border-color:var(--grid-soft)}
  .matrix > div:nth-child(6n){border-right:none}
  .matrix--technique > div:nth-child(4n),.matrix--priority > div:nth-child(3n){border-right:none}
  .matrix--technique > div:nth-child(6n){border-right:1px solid var(--grid-soft)}
  .matrix--technique > div:nth-child(4n){border-right:none}
  .matrix--priority > div:nth-child(6n){border-right:none}
  .head{display:flex;align-items:center;justify-content:center;background:var(--paper);font-size:6.5px;font-weight:700}
  .head svg{width:18px;height:16px}
  .cell--shade{background:var(--row-shade)}
  .cell--plain{background:var(--paper)}
  .matrix > .last{border-bottom:none}

  .stages{left:0;top:722px;width:1200px;height:52px}
  .stage-label{font-size:19px;font-weight:600;fill:var(--ink);font-family:"Nunito Sans",Arial,sans-serif}

  .footer{left:31px;top:800px;font-size:10.5px}
  .footer strong{font-size:13px;font-weight:700}
</style>
</head>
<body>
<main class="sheet">
  <h1 class="abs title">Project&nbsp; Communication Strategy Model</h1>
  <div class="abs brand"><span class="brand-mark"></span>Brightline Communications</div>

  <svg class="abs flow-lines" viewBox="0 0 1200 848" aria-hidden="true">
    <g stroke="var(--green-line)" stroke-width="7" fill="none">
      <line x1="590" y1="150" x2="590" y2="205"/>
      <polyline points="832,227 138,227 138,398"/>
    </g>
    <polygon points="124,396 152,396 138,414" fill="var(--green-line)"/>
    <rect x="572" y="209" width="36" height="36" rx="4" transform="rotate(45 590 227)" fill="var(--dark-box)"/>
  </svg>

  <div class="abs node node--event">Event</div>
  <div class="abs question">Reportable?</div>
  <div class="abs node node--yes">Yes</div>
  <div class="abs node node--no">No</div>
  <div class="abs node node--end">End</div>

  <div class="abs section-bar bar--channel">Channel</div>
  <div class="abs section-bar bar--medium">Medium</div>
  <div class="abs section-bar bar--delivery">Delivery</div>
  <div class="abs sub-bar sub--technique">Influencing Technique</div>
  <div class="abs sub-bar sub--priority">Priority</div>

  <section class="abs audience audience--management">
    <div class="audience-id">
      <svg viewBox="0 0 50 54" aria-hidden="true"><polygon points="25,3 47,26 35,26 35,51 15,51 15,26 3,26" fill="none" stroke="var(--green)" stroke-width="1.6" stroke-linejoin="round"/></svg>
      <span class="audience-name">Management</span>
    </div>
    <ol class="audience-list"><li>1)<span></span></li><li>2)<span></span></li><li>3)<span></span></li><li>4)<span></span></li><li>5)<span></span></li></ol>
  </section>
  <section class="abs audience audience--stakeholders">
    <div class="audience-id">
      <svg viewBox="0 0 54 50" aria-hidden="true"><polygon points="51,25 28,3 28,15 3,15 3,35 28,35 28,47" fill="none" stroke="var(--green)" stroke-width="1.6" stroke-linejoin="round"/></svg>
      <span class="audience-name">Stakeholders</span>
    </div>
    <ol class="audience-list"><li>1)<span></span></li><li>2)<span></span></li><li>3)<span></span></li><li>4)<span></span></li><li>5)<span></span></li></ol>
  </section>
  <section class="abs audience audience--team">
    <div class="audience-id">
      <svg viewBox="0 0 50 54" aria-hidden="true"><polygon points="25,51 47,28 35,28 35,3 15,3 15,28 3,28" fill="none" stroke="var(--green)" stroke-width="1.6" stroke-linejoin="round"/></svg>
      <span class="audience-name">Project Team</span>
    </div>
    <ol class="audience-list"><li>1)<span></span></li><li>2)<span></span></li><li>3)<span></span></li><li>4)<span></span></li><li>5)<span></span></li></ol>
  </section>

  <div class="abs medium-labels">
    <span>Email</span><span>Phone</span><span>Meeting</span><span>System</span><span>Report</span><span>Presentation</span>
  </div>

  <div class="abs matrix matrix--medium">
    <div class="head"><svg viewBox="0 0 18 16"><rect x="2" y="3" width="14" height="10" fill="none" stroke="#333" stroke-width="1.4"/><polyline points="2,3 9,9 16,3" fill="none" stroke="#333" stroke-width="1.4"/></svg></div>
    <div class="head"><svg viewBox="0 0 18 16"><path d="M5 2 L7.5 2 L8.5 5 L7 6.5 Q8.5 9.5 11.5 11 L13 9.5 L16 10.5 L16 13 Q15 14.5 13 14 Q5 11.5 3.5 4 Q3.5 2.5 5 2Z" fill="#333"/></svg></div>
    <div class="head"><svg viewBox="0 0 18 16"><circle cx="5" cy="5" r="2" fill="#333"/><circle cx="9" cy="4" r="2.3" fill="#333"/><circle cx="13" cy="5" r="2" fill="#333"/><path d="M2 13 Q2 8 5 8 Q8 8 8 13Z M5.5 13 Q5.5 7 9 7 Q12.5 7 12.5 13Z M10 13 Q10 8 13 8 Q16 8 16 13Z" fill="#333"/></svg></div>
    <div class="head"><svg viewBox="0 0 18 16"><rect x="2" y="2" width="14" height="12" fill="none" stroke="#333" stroke-width="1.4"/><line x1="2" y1="5" x2="16" y2="5" stroke="#333" stroke-width="1.4"/><rect x="4" y="7" width="4" height="5" fill="#333"/><rect x="10" y="7" width="4" height="2" fill="#333"/></svg></div>
    <div class="head"><svg viewBox="0 0 18 16"><path d="M2 3 L7 3 L8.5 5 L16 5 L16 14 L2 14Z" fill="#333"/></svg></div>
    <div class="head"><svg viewBox="0 0 18 16"><rect x="3" y="2" width="12" height="9" fill="none" stroke="#333" stroke-width="1.4"/><rect x="1" y="12" width="16" height="2" fill="#333"/></svg></div>
    <div class="cell--shade"></div><div class="cell--shade"></div><div class="cell--shade"></div><div class="cell--shade"></div><div class="cell--shade"></div><div class="cell--shade"></div>
    <div class="cell--plain"></div><div class="cell--plain"></div><div class="cell--plain"></div><div class="cell--plain"></div><div class="cell--plain"></div><div class="cell--plain"></div>
    <div class="cell--shade last"></div><div class="cell--shade last"></div><div class="cell--shade last"></div><div class="cell--shade last"></div><div class="cell--shade last"></div><div class="cell--shade last"></div>
  </div>

  <div class="abs matrix matrix--technique">
    <div class="head">Rational</div><div class="head">Emotional</div><div class="head">Coordination</div><div class="head">Collaboration</div>
    <div class="cell--shade"></div><div class="cell--shade"></div><div class="cell--shade"></div><div class="cell--shade"></div>
    <div class="cell--plain"></div><div class="cell--plain"></div><div class="cell--plain"></div><div class="cell--plain"></div>
    <div class="cell--shade last"></div><div class="cell--shade last"></div><div class="cell--shade last"></div><div class="cell--shade last"></div>
  </div>

  <div class="abs matrix matrix--priority">
    <div class="head">High</div><div class="head">Medium</div><div class="head">Low</div>
    <div class="cell--shade"></div><div class="cell--shade"></div><div class="cell--shade"></div>
    <div class="cell--plain"></div><div class="cell--plain"></div><div class="cell--plain"></div>
    <div class="cell--shade last"></div><div class="cell--shade last"></div><div class="cell--shade last"></div>
  </div>

  <svg class="abs stages" viewBox="0 0 1200 52" aria-label="Who, What, How, When">
    <g fill="#fff" stroke="var(--green)" stroke-width="1.6" stroke-linejoin="round">
      <polygon points="1,3 258,3 278,26 258,49 1,49"/>
      <polygon points="268,3 778,3 798,26 778,49 268,49 288,26"/>
      <polygon points="785,3 1011,3 1031,26 1011,49 785,49 805,26"/>
      <polygon points="1019,3 1170,3 1190,26 1170,49 1019,49 1039,26"/>
    </g>
    <text class="stage-label" x="140" y="33" text-anchor="middle">Who</text>
    <text class="stage-label" x="527" y="33" text-anchor="middle">What</text>
    <text class="stage-label" x="896" y="33" text-anchor="middle">How</text>
    <text class="stage-label" x="1098" y="33" text-anchor="middle">When</text>
  </svg>

  <p class="abs footer"><strong>Brightline Communications Pty. Ltd</strong> / www.brightlinecomms.example / PO Box 418, Harbourview NSW 2099 / +61 2 9000 1357&nbsp; ABN: 12 345 678 901</p>
</main>
</body>
</html>
```